Business Card Design for Software Development Company

I am looking for a business card design the incorporates my new logo (attached below).

Key information to include:
Name: Martin Quelbrook
Title: CEO
Email: martin@brightwellcivic.example
Phone: 555-218-9403
Website: www.brightwellcivic.example

NOTE: This design should be easy to edit so that we can order cards for different members of our team.

```html
<!DOCTYPE html>
<html lang="en">
<head>
<meta charset="utf-8">
<title>Brightwell Labs Business Card</title>
<link href="https://fonts.googleapis.com/css2?family=Montserrat:wght@400;500;700&display=swap" rel="stylesheet">
<style>
  :root {
    --stage: #1c1c1c;
    --card-front: #f4f4f4;
    --card-back: #202020;
    --ink: #1f1f1f;
    --teal: #17a78f;
    --orange: #e67a22;
    --peach: #f3d9c4;
    --mint: #bfe8e0;
    --rose: #efcfd2;
    --back-mark: #6c6c6c;
  }
  html, body {
    margin: 0;
    padding: 0;
    width: 1200px;
    height: 1059px;
    overflow: hidden;
    background: var(--stage);
    font-family: "Montserrat", sans-serif;
  }
  .card {
    position: absolute;
    border-radius: 18px;
    overflow: hidden;
  }
  .card--front {
    left: 257px;
    top: 89px;
    width: 687px;
    height: 390px;
    background: var(--card-front);
    color: var(--ink);
  }
  .card--back {
    left: 254px;
    top: 547px;
    width: 693px;
    height: 393px;
    background: var(--card-back);
  }
  .artwork-area {
    position: absolute;
    right: 0;
    top: 0;
    width: 150px;
    height: 390px;
    background: linear-gradient(180deg, var(--mint) 0%, var(--rose) 50%, var(--peach) 100%);
  }
  .brand {
    position: absolute;
    display: flex;
    align-items: center;
    gap: 10px;
    font-weight: 700;
    white-space: nowrap;
  }
  .brand__dot {
    border-radius: 50%;
    background: var(--teal);
  }
  .card--front .brand {
    left: 39px;
    top: 68px;
    font-size: 36px;
    letter-spacing: -0.5px;
    color: var(--ink);
  }
  .card--front .brand__dot { width: 24px; height: 24px; }
  .card--back .brand {
    left: 89px;
    top: 166px;
    font-size: 56px;
    letter-spacing: -0.5px;
    color: var(--back-mark);
  }
  .card--back .brand__dot { width: 36px; height: 36px; }
  .name-tab {
    position: absolute;
    left: 0;
    top: 188px;
    width: 18px;
    height: 41px;
    background: var(--teal);
    border-radius: 0 3px 3px 0;
  }
  .person {
    position: absolute;
    left: 39px;
    top: 184px;
  }
  .person__name {
    margin: 0;
    font-size: 23px;
    font-weight: 700;
    line-height: 1.1;
    letter-spacing: 0.2px;
    text-transform: uppercase;
  }
  .person__first { color: var(--teal); }
  .person__last { color: var(--orange); }
  .person__title {
    margin: 2px 0 0;
    font-size: 17px;
    font-weight: 400;
  }
  .contacts {
    position: absolute;
    left: 38px;
    top: 263px;
    margin: 0;
    padding: 0;
    list-style: none;
  }
  .contacts__item {
    display: flex;
    align-items: center;
    gap: 8px;
    height: 32.5px;
    font-size: 17.5px;
    font-weight: 400;
  }
  .contacts__icon { width: 14px; height: 14px; flex: none; }
</style>
</head>
<body>
  <section class="card card--front">
    <div class="artwork-area" role="img" aria-label="Decorative artwork area in soft mint, rose and peach tones"></div>

    <div class="brand"><span class="brand__dot"></span>Brightwell Labs</div>

    <div class="name-tab"></div>
    <div class="person">
      <h1 class="person__name"><span class="person__first">Martin</span> <span class="person__last">Quelbrook</span></h1>
      <p class="person__title">CEO</p>
    </div>

    <ul class="contacts">
      <li class="contacts__item">
        <svg class="contacts__icon" viewBox="0 0 14 14" aria-hidden="true"><path d="M1 5c0-2 2.5-3 6-3s6 1 6 3v1h-3V4.5H4V6H1z M3 7h8l1.5 5h-11z" fill="#f3c9a4"/></svg>
        <span>555-218-9403</span>
      </li>
      <li class="contacts__item">
        <svg class="contacts__icon" viewBox="0 0 14 14" aria-hidden="true"><path d="M1 6l6-4 6 4v7H1z" fill="var(--teal)"/><path d="M1 6l6 4 6-4" fill="none" stroke="#fff" stroke-width="1"/></svg>
        <span>martin@brightwellcivic.example</span>
      </li>
      <li class="contacts__item">
        <svg class="contacts__icon" viewBox="0 0 14 14" aria-hidden="true"><circle cx="7" cy="7" r="6" fill="var(--orange)"/><path d="M4 3c2 1 1 3 3 3s1 3 0 4M9 2c0 2 2 2 3 3" fill="none" stroke="#fff" stroke-width="1"/></svg>
        <span>www.brightwellcivic.example</span>
      </li>
    </ul>
  </section>

  <section class="card card--back">
    <div class="brand"><span class="brand__dot"></span>Brightwell Labs</div>
  </section>
</body>
</html>
```